A gateway to the eyes of potential Talquen Candidates and Clients

We are looking for a brochure that will grab attention, all most along the lines of an infogram. The business supplies people to the construction sector. So we want it simple but sharp.

I would like the brochure to be able to have a half fold effect when printed but the main focus will be to use it in an e-brochure format.

Main pages will be as follows:

About Us: Which will have a bit about the management team and some pictures.

Services: information for both candidate and clients.

Why us?:

Contact: Location, contact numbers etc.

FOR CONTENTS:
website will give you the content required. www.talquenbuilders.co.uk
Updates

Project Deadline Extended Reason: Project was moved from a flyer to a brochure and the logo didn't upload. So I will be uploading my new logo and it will give additional time to get designs in. Cheers Added Monday, June 20, 2016

Target Market(s)

Clients and candidates for the construction market

Industry/Entity Type

Business

Requirements
Must have
• Bold and strong images of the construction sector. A simple to read format. Also needs to look good in an electronic format.
Nice to have
• I like the idea of a black and white model but with certain parts of the images highlighted in our colours.
Should not have
• Too much of a complex lay out.

```html
<!DOCTYPE html>
<html lang="en">
<head>
<meta charset="utf-8">
<title>Talquen Builders – Brochure Spread</title>
<link rel="stylesheet" href="https://fonts.googleapis.com/css2?family=Open+Sans:wght@300;400;600;700&display=swap">
<style>
  :root {
    --brand-blue: #2d62a3;
    --brand-blue-light: #3f8fd2;
    --brand-orange: #e8962a;
    --ink: #3a3f47;
    --ink-soft: #6b717a;
    --paper: #ffffff;
    --backdrop: #e4e4e2;
    --facet: #eef1f5;
  }
  * { box-sizing: border-box; margin: 0; padding: 0; }
  html, body { width: 1200px; height: 804px; overflow: hidden; }
  body {
    background: var(--backdrop);
    font-family: "Open Sans", sans-serif;
    color: var(--ink);
  }
  .spread {
    position: absolute;
    left: 40px; top: 22px;
    width: 1120px; height: 760px;
    display: flex;
    box-shadow: 0 6px 24px rgba(0,0,0,.18);
  }
  .page {
    position: relative;
    width: 560px; height: 760px;
    background: var(--paper);
    overflow: hidden;
  }
  .page--left { background: linear-gradient(90deg, #fff 85%, #eceef1 100%); }
  .page--right { background: linear-gradient(90deg, #e6e9ed 0%, #fff 12%); }
  .facets { position: absolute; inset: 0; }
  .hero {
    position: absolute;
    left: 40px; top: 50px;
    width: 480px; height: 250px;
  }
  .hero__image { position: absolute; inset: 0; }
  .hero__image--plans { background: linear-gradient(135deg, #c9d3ea 0%, #8fa2cf 45%, #5f74ad 100%); }
  .hero__image--site { background: linear-gradient(180deg, #5d8fd8 0%, #a8c6ee 55%, #dfe8f2 100%); }
  .hero__band {
    position: absolute;
    left: 24px; right: 0; bottom: -12px;
    height: 12px;
    background: var(--brand-blue);
  }
  .hero__band::after {
    content: "";
    position: absolute;
    left: 0; top: 12px;
    border-left: 8px solid transparent;
    border-right: 8px solid transparent;
    border-top: 8px solid var(--brand-blue);
  }
  .section-tab {
    position: absolute;
    left: -6px; top: -8px;
    width: 70px; height: 34px;
    background: var(--brand-orange);
    clip-path: polygon(0 0, 72% 0, 100% 100%, 0 100%);
    color: #fff;
    font-weight: 700;
    font-size: 22px;
    line-height: 34px;
    padding-left: 10px;
  }
  .content { position: absolute; left: 66px; right: 40px; }
  .page-title {
    font-weight: 700;
    font-size: 30px;
    letter-spacing: -.5px;
    color: var(--brand-blue);
  }
  .page-title .accent { color: var(--brand-orange); }
  .page-title .lead-word { color: var(--brand-blue-light); }
  .intro {
    margin-top: 14px;
    font-weight: 300;
    font-size: 17px;
    line-height: 1.4;
    color: var(--ink-soft);
  }
  .body-copy {
    font-size: 10.5px;
    line-height: 1.62;
    color: var(--ink);
  }
  .body-copy + .body-copy { margin-top: 12px; }
  .dropcap::first-letter {
    float: left;
    font-size: 58px;
    line-height: .86;
    font-weight: 600;
    margin: 4px 8px 0 0;
    color: var(--ink);
  }
  .sub-heading {
    font-weight: 700;
    font-size: 16px;
    text-transform: uppercase;
    color: #2b2f35;
    margin-bottom: 8px;
  }
  .sub-heading--spaced { margin-top: 22px; }
  .footer-band {
    position: absolute;
    left: 0; right: 0; bottom: 0;
    height: 40px;
    background: var(--brand-blue);
  }
  .web-strip {
    position: absolute;
    bottom: 40px; height: 22px;
    display: flex; align-items: center; gap: 8px;
    font-size: 10px;
    color: var(--brand-blue);
  }
  .page--left .web-strip { right: 30px; }
  .page--right .web-strip { left: 30px; }
  .web-strip__dot {
    width: 9px; height: 9px; border-radius: 50%;
    background: var(--brand-orange);
  }
  .page-number {
    position: absolute;
    bottom: 9px;
    width: 26px; height: 22px;
    border: 1px solid #fff;
    color: #fff;
    font-size: 12px;
    text-align: center;
    line-height: 20px;
  }
  .page--left .page-number { left: 24px; }
  .page--right .page-number { right: 24px; }
</style>
</head>
<body>
<main class="spread">

  <section class="page page--left">
    <svg class="facets" viewBox="0 0 560 760" aria-hidden="true">
      <polygon points="0,300 220,540 0,760" fill="var(--facet)"/>
      <polygon points="340,330 470,420 360,470" fill="var(--facet)"/>
    </svg>

    <figure class="hero">
      <div class="hero__image hero__image--plans" role="img" aria-label="Photo of a yellow hard hat and folding ruler resting on rolled building blueprints"></div>
      <div class="hero__band"></div>
      <span class="section-tab">01</span>
    </figure>

    <div class="content" style="top:350px;">
      <h1 class="page-title">ABOUT <span class="accent">US</span></h1>
      <p class="intro">Fresh start? New Job? Brighter Future? A Better you? Talquen Construction is in your corner.</p>
    </div>

    <div class="content" style="top:470px;">
      <p class="body-copy dropcap">Established in 2016, Talquen Construction has already been recognised as a market-leading specialist for contract and permanent recruitment both domestically and internationally. Our core focus is on delivering professional people into the following key areas, Project, Design, Surveying and we also deliver hand picked teams for the trades and labour. Due to our partnerships around Europe we have access to a huge pool of skilled candidates from the far reaches of Europe.</p>
      <p class="body-copy">Our success is down to the dedicated consultants that offer a combination of well proactive approach and the ability to source candidates that are passive in the market place. Each one of them is experienced in their field and trained in executive search and selection methodology. That means you'll only ever deal with someone who has a thorough understanding of their candidates' and clients' needs. Add in our ethos of 'Innovation, Motivation, Dedication, as well as our core values of hard work and professionalism and the result is a genuine ability to deliver a truly dynamic recruitment service.</p>
    </div>

    <div class="web-strip"><span class="web-strip__dot"></span>www.talquenbuilders.co.uk</div>
    <div class="footer-band"></div>
    <span class="page-number">02</span>
  </section>

  <section class="page page--right">
    <svg class="facets" viewBox="0 0 560 760" aria-hidden="true">
      <polygon points="560,280 360,520 560,700" fill="var(--facet)"/>
      <polygon points="40,320 170,400 60,440" fill="var(--facet)"/>
    </svg>

    <figure class="hero">
      <div class="hero__image hero__image--site" role="img" aria-label="Photo of a yellow surveying instrument on a tripod beneath a tower crane against a cloudy blue sky"></div>
      <div class="hero__band"></div>
      <span class="section-tab">02</span>
    </figure>

    <div class="content" style="top:340px;">
      <h1 class="page-title"><span class="lead-word">WHY</span> <span class="accent">TALQUEN?</span></h1>
    </div>

    <div class="content" style="top:394px;">
      <h2 class="sub-heading">Why choose our services</h2>
      <p class="body-copy">Why us? Because in this world you need pro-active people in your corner. Talquen are that and so much more...</p>
      <p class="body-copy">With a large network, Talquen offers a dynamic approach and a large international network of decision makers and exclusive candidates.</p>
      <p class="body-copy">Our clients benefit from a single point of contact and a tailored growth plan to match their own corporate strategy. The question is, why haven't you made contact with us already?</p>

      <h2 class="sub-heading sub-heading--spaced">Our obligation</h2>
      <p class="body-copy">Our reputation is our brand and our brand our reputation. Clients and Candidates are always treated with the upmost professionalism and all contact is of a private and confidential nature.</p>
      <p class="body-copy">In a market that has a lot of bad press we at Talquen are out to change peoples opinions of recruitment and be an outsource partner of choice.</p>
    </div>

    <div class="web-strip"><span class="web-strip__dot"></span>www.talquenbuilders.co.uk</div>
    <div class="footer-band"></div>
    <span class="page-number">03</span>
  </section>

</main>
</body>
</html>
```